Redesign of business card for Cedar Ridge Mechanical

We are looking for a new design for our business cards for Cedar Ridge Mechanical. We are a plumbing & HVAC construction company, operating on the West Coast of Canada and USA. Logo attached.
Industry/Entity Type
Construction - Plumbing & HVAC
Contact Information for Business Card
Name, address, phone numbers, email, website address
Look and feel
Each slider illustrates characteristics of the customer's brand and the style your logo design should communicate.

```html
<!DOCTYPE html>
<html lang="en">
<head>
<meta charset="utf-8">
<title>Cedar Ridge Mechanical – Business Card</title>
<link rel="stylesheet" href="https://fonts.googleapis.com/css2?family=Poppins:wght@300;400;700&display=swap">
<style>
  :root {
    --stage: #2a2a2c;
    --card: #222326;
    --frame: #ffffff;
    --ink: #ffffff;
  }
  * { box-sizing: border-box; margin: 0; padding: 0; }
  html, body { width: 1200px; height: 711px; overflow: hidden; }
  body {
    background: var(--stage);
    font-family: "Poppins", sans-serif;
    color: var(--ink);
    display: flex;
    align-items: center;
    justify-content: center;
    gap: 40px;
  }
  .card {
    position: relative;
    width: 540px;
    height: 310px;
    border-radius: 24px;
    background: var(--frame);
    padding: 10px;
  }
  .card__panel {
    position: relative;
    width: 100%;
    height: 100%;
    border-radius: 14px;
    background: var(--card);
  }
  .frame-break {
    position: absolute;
    background: var(--card);
  }
  .frame-break--top-left { top: 0; left: 28px; width: 6px; height: 10px; }
  .frame-break--top-right { top: 0; right: 28px; width: 6px; height: 10px; }
  .frame-break--bottom-left { bottom: 0; left: 28px; width: 6px; height: 10px; }
  .frame-break--bottom-right { bottom: 0; right: 28px; width: 6px; height: 10px; }

  .brand {
    display: flex;
    align-items: center;
    gap: 10px;
  }
  .brand__mark {
    width: 22px;
    height: 22px;
    background: var(--ink);
    flex: none;
  }
  .brand__name {
    font-weight: 700;
    text-transform: uppercase;
    letter-spacing: 0.04em;
    line-height: 1.1;
  }

  .card--front .card__panel {
    display: flex;
    align-items: center;
    justify-content: center;
  }
  .card--front .brand__name { font-size: 26px; }
  .card--front .brand__mark { width: 30px; height: 30px; }

  .card--back .brand {
    position: absolute;
    top: 34px;
    right: 30px;
  }
  .card--back .brand__name { font-size: 17px; }

  .contact {
    position: absolute;
    left: 30px;
    bottom: 26px;
  }
  .contact__name {
    font-size: 24px;
    font-weight: 300;
    line-height: 1.1;
  }
  .contact__name strong { font-weight: 700; }
  .contact__role {
    font-size: 11px;
    font-weight: 400;
    margin: 3px 0 10px 14px;
  }
  .contact__address {
    font-size: 11px;
    font-weight: 400;
    line-height: 1.4;
    margin: 0 0 10px 14px;
    font-style: normal;
  }
  .contact__list { list-style: none; margin-left: 0; }
  .contact__item {
    display: flex;
    align-items: center;
    gap: 8px;
    font-size: 11px;
    line-height: 1.6;
  }
  .contact__icon { width: 10px; height: 10px; flex: none; }
</style>
</head>
<body>
  <section class="card card--front" aria-label="Card front">
    <span class="frame-break frame-break--top-left"></span>
    <span class="frame-break frame-break--top-right"></span>
    <span class="frame-break frame-break--bottom-left"></span>
    <span class="frame-break frame-break--bottom-right"></span>
    <div class="card__panel">
      <div class="brand">
        <span class="brand__mark"></span>
        <span class="brand__name">Cedar Ridge Mechanical</span>
      </div>
    </div>
  </section>

  <section class="card card--back" aria-label="Card back">
    <span class="frame-break frame-break--top-left"></span>
    <span class="frame-break frame-break--top-right"></span>
    <span class="frame-break frame-break--bottom-left"></span>
    <span class="frame-break frame-break--bottom-right"></span>
    <div class="card__panel">
      <div class="brand">
        <span class="brand__mark"></span>
        <span class="brand__name">Cedar Ridge Mechanical</span>
      </div>

      <div class="contact">
        <h1 class="contact__name"><strong>Marta</strong> Kovacs</h1>
        <p class="contact__role">Founder &amp; CEO</p>
        <address class="contact__address">418 Harbor Ln. Suite 310<br>Tacoma, WA 98402</address>
        <ul class="contact__list">
          <li class="contact__item">
            <svg class="contact__icon" viewBox="0 0 10 10" aria-hidden="true"><path d="M2 1 L3.6 1 L4.3 3 L3.3 3.8 Q4.2 5.8 6.2 6.7 L7 5.7 L9 6.4 L9 8 Q9 9 8 9 Q1 8.5 1 2 Q1 1 2 1 Z" fill="#fff"/></svg>
            (253) 555-0147
          </li>
          <li class="contact__item">
            <svg class="contact__icon" viewBox="0 0 10 10" aria-hidden="true"><rect x="0.5" y="1.5" width="9" height="7" fill="none" stroke="#fff"/><path d="M0.5 1.5 L5 5.5 L9.5 1.5" fill="none" stroke="#fff"/></svg>
            info@cedarridgemech.com
          </li>
          <li class="contact__item">
            <svg class="contact__icon" viewBox="0 0 10 10" aria-hidden="true"><circle cx="5" cy="5" r="4.3" fill="none" stroke="#fff"/><ellipse cx="5" cy="5" rx="1.8" ry="4.3" fill="none" stroke="#fff"/><path d="M0.7 5 H9.3" stroke="#fff"/></svg>
            www.cedarridgemech.com
          </li>
        </ul>
      </div>
    </div>
  </section>
</body>
</html>
```